Business card for builder specialising in renovations.

Need a card for our building business. Business name is under Martin Powles.
Have licence number on card ( 527691K)
Contact number (0400 382 415)
Want to work on logo for some business cards and shirts - something with MP or MPB or open to ideas??
No animations, No hammers. Something sharp and eye catching.
Highlight that we are a renovation specialist. Simple on front with extra details on back with some lines to jot down things.

Target Market(s)

Renovators

Industry/Entity Type

Building

Contact Information for Business Card

2 sided with room on back to jot things down.
Extra details on back so front can be simple ..like, renovations, bathrooms, decks, extensions, new builds,

Logo Text

MP

Font styles to use
Serif

Requirements
Must have
• Eye catching design .
• Name : Martin powles
• Licence number
• Contact number - 0400382415
Nice to have
• Some logo design that we can carry through to other forms of advertising
• Local builder
• Quality work
Should not have
• No animations

```html
<!DOCTYPE html>
<html lang="en">
<head>
<meta charset="utf-8">
<title>Martin Powles – Business Card</title>
<link rel="stylesheet" href="https://fonts.googleapis.com/css2?family=Tinos:wght@400;700&display=swap">
<style>
  :root {
    --backdrop: #2b2b2d;
    --card-white: #ffffff;
    --card-black: #000000;
    --brand-blue: #1776c2;
    --ink: #111111;
    --text-light: #ffffff;
  }
  * { box-sizing: border-box; margin: 0; padding: 0; }
  html, body {
    width: 1200px; height: 900px; overflow: hidden;
    background: var(--backdrop);
    font-family: "Tinos", "Times New Roman", serif;
  }
  .canvas { position: relative; width: 1200px; height: 900px; }
  .card {
    position: absolute; width: 640px; height: 366px; overflow: hidden;
  }

  /* Front */
  .card-front {
    left: 90px; top: 70px; background: var(--card-white);
    display: flex; flex-direction: column; align-items: center;
  }
  .brand-mark {
    margin-top: 78px; display: flex; align-items: center; gap: 14px;
    color: var(--brand-blue); font-size: 54px; font-weight: 400; letter-spacing: 2px;
  }
  .brand-mark .mark-square {
    width: 22px; height: 22px; border: 3px solid var(--brand-blue);
  }
  .services-pill {
    margin-top: 44px; padding: 4px 16px;
    border: 1.5px solid var(--brand-blue); border-radius: 14px;
    font-size: 15px; letter-spacing: 0.3px; color: var(--ink); white-space: nowrap;
  }
  .front-web { margin-top: 12px; font-size: 17px; color: var(--ink); }
  .accent { color: var(--brand-blue); }

  /* Back */
  .card-back { left: 470px; top: 464px; background: var(--card-black); }
  .back-panel {
    position: absolute; left: 0; top: 0; width: 350px; height: 366px;
    background: var(--card-white);
    border: 14px solid var(--brand-blue); border-right: none;
    display: flex; align-items: center; justify-content: center;
  }
  .back-panel .panel-name {
    font-size: 34px; color: var(--brand-blue); letter-spacing: 1px;
  }
  .back-details {
    position: absolute; right: 32px; top: 54px; width: 250px;
    text-align: right; color: var(--text-light); font-size: 15px; line-height: 1.32;
  }
  .person-name {
    font-size: 22px; color: var(--brand-blue); letter-spacing: 0.5px; line-height: 1.1;
  }
  .person-role { margin-bottom: 6px; }
  .contact-row { display: flex; justify-content: flex-end; align-items: center; gap: 7px; }
  .contact-row svg { width: 11px; height: 11px; fill: var(--brand-blue); flex: none; }
  .contact-row .spacer { width: 11px; flex: none; }
</style>
</head>
<body>
<main class="canvas">

  <section class="card card-front" aria-label="Card front">
    <div class="brand-mark"><span class="mark-square"></span>Martin Powles</div>
    <p class="services-pill">RENOVATIONS, BATHROOMS, DECKS, EXTENSIONS, NEW BUILDS,</p>
    <p class="front-web">www.<span class="accent">martinpowles</span>.com</p>
  </section>

  <section class="card card-back" aria-label="Card back">
    <div class="back-panel">
      <span class="panel-name">Martin Powles</span>
    </div>
    <div class="back-details">
      <p class="person-name">MARTIN POWLES</p>
      <p class="person-role">Director</p>
      <p class="contact-row"><span><span class="accent">Licence:</span> (527691K)</span><span class="spacer"></span></p>
      <p class="contact-row">0400382415
        <svg viewBox="0 0 24 24" aria-hidden="true"><path d="M6.6 10.8a15.1 15.1 0 0 0 6.6 6.6l2.2-2.2a1 1 0 0 1 1-.25 11.4 11.4 0 0 0 3.6.57 1 1 0 0 1 1 1V20a1 1 0 0 1-1 1A17 17 0 0 1 3 4a1 1 0 0 1 1-1h3.5a1 1 0 0 1 1 1c0 1.25.2 2.45.57 3.57a1 1 0 0 1-.25 1z"/></svg>
      </p>
      <p class="contact-row">info@martinpowles.com
        <svg viewBox="0 0 24 24" aria-hidden="true"><path d="M2 5h20v14H2z M4 7v.5l8 5 8-5V7l-8 5z" fill-rule="evenodd"/></svg>
      </p>
      <p class="contact-row">www.<span class="accent">martinpowles</span>.com
        <svg viewBox="0 0 24 24" aria-hidden="true"><circle cx="12" cy="12" r="10"/></svg>
      </p>
    </div>
  </section>

</main>
</body>
</html>
```